Corporate Business Card

Very professional, Modern, Not to busy, include phone address email, website
(253) 617-4930, 18761 52nd Avenue S, Kent, WA 98047, martin@plumlinegroup.com, varkoworks.com

Target Market(s)

Manufacturing

Industry/Entity Type

Aero, machining, manufacturing, Off road racing

Contact Information for Business Card

Phone, address email, website

```html
<!DOCTYPE html>
<html lang="en">
<head>
<meta charset="utf-8">
<title>Varko Works – Business Card</title>
<link href="https://fonts.googleapis.com/css2?family=Poppins:wght@400;700&display=swap" rel="stylesheet">
<style>
  :root {
    --navy: #16336b;
    --white: #ffffff;
    --backdrop: #e4e6ea;
  }
  * { margin: 0; padding: 0; box-sizing: border-box; }
  html, body {
    width: 1200px; height: 1200px; overflow: hidden;
    background: var(--backdrop);
    font-family: "Poppins", sans-serif;
  }
  .sheet {
    position: relative; width: 1200px; height: 1200px;
    display: flex; flex-direction: column; align-items: center; justify-content: center; gap: 60px;
  }
  .card {
    position: relative; width: 900px; height: 515px;
    background: var(--white); border-radius: 31px;
  }
  .card__frame {
    position: absolute; inset: 32px;
    border: 2px solid var(--navy); border-radius: 24px; overflow: hidden;
  }
  .brand {
    position: absolute; left: 0; right: 0;
    text-align: center; color: var(--navy);
    font-weight: 700; letter-spacing: 1px; white-space: nowrap;
  }
  .card--front .brand { top: 50%; transform: translateY(-55%); font-size: 64px; }
  .card--back .brand { top: 82px; font-size: 40px; }
  .contact-band {
    position: absolute; left: 0; right: 0; top: 224px; bottom: 0;
    background: var(--navy); color: var(--white);
  }
  .icon-row { position: absolute; left: 0; top: 0; width: 836px; height: 120px; }
  .contact-lines {
    position: absolute; left: 0; right: 0; top: 108px;
    display: grid; grid-template-columns: 1fr 1fr; column-gap: 24px;
    font-size: 20.5px; line-height: 34px; font-weight: 400;
  }
  .contact-lines .col-left { text-align: right; }
  .contact-lines .col-right { text-align: left; }
</style>
</head>
<body>
<main class="sheet">

  <section class="card card--front" aria-label="Card front">
    <div class="card__frame">
      <div class="brand">Varko Works</div>
    </div>
  </section>

  <section class="card card--back" aria-label="Card back">
    <div class="card__frame">
      <div class="brand">Varko Works</div>
      <div class="contact-band">
        <svg class="icon-row" viewBox="0 0 836 120" aria-hidden="true">
          <g stroke="#ffffff" stroke-width="2" fill="none">
            <line x1="215" y1="57" x2="622" y2="57"/>
          </g>
          <g fill="#ffffff" stroke="#16336b" stroke-width="2">
            <circle cx="335" cy="57" r="17"/>
            <circle cx="390" cy="57" r="17"/>
            <circle cx="446" cy="57" r="17"/>
            <circle cx="501" cy="57" r="17"/>
          </g>
          <!-- phone -->
          <path d="M328 49 q2 -2 4 0 l2 3 q1 2 -1 3 q1 4 5 6 q1 -2 3 -1 l3 2 q2 2 0 4 q-2 2 -5 1 q-9 -4 -12 -13 q-1 -3 1 -5z" fill="#16336b"/>
          <path d="M337 48 a7 7 0 0 1 6 6 M338 44 a11 11 0 0 1 9 9" stroke="#16336b" stroke-width="1.4" fill="none"/>
          <!-- mail -->
          <g stroke="#16336b" stroke-width="1.8" fill="none">
            <rect x="380" y="50" width="20" height="14" rx="1.5"/>
            <path d="M380 51 l10 7 l10 -7 M380 64 l7 -6 M400 64 l-7 -6"/>
          </g>
          <!-- pin -->
          <path d="M446 46 a7 7 0 0 1 7 7 c0 5 -7 12 -7 12 s-7 -7 -7 -12 a7 7 0 0 1 7 -7z" fill="#16336b"/>
          <circle cx="446" cy="53" r="2.6" fill="#ffffff"/>
          <ellipse cx="446" cy="67" rx="7" ry="2" fill="none" stroke="#16336b" stroke-width="1.4"/>
          <!-- globe -->
          <g stroke="#16336b" stroke-width="1.5" fill="none">
            <circle cx="501" cy="57" r="9"/>
            <ellipse cx="501" cy="57" rx="4" ry="9"/>
            <path d="M492 57 h18 M494 52 h14 M494 62 h14"/>
          </g>
        </svg>
        <div class="contact-lines">
          <div class="col-left">(253) 617-4930, 18761</div>
          <div class="col-right">varkoworks.com</div>
          <div class="col-left">martin@plumlinegroup.com</div>
          <div class="col-right">52nd Avenue S, Kent, WA 98047</div>
        </div>
      </div>
    </div>
  </section>

</main>
</body>
</html>
```